Business Card Design Project

i need a bussines car design
Velora Clinical Hypnotherapy

Daniel Wexford
Psychotherapy & Hypnosis

84261937 /0427591628

back of the card appoinment space.

file was provided on a PDF, LOgo , use the blu colorsa as well , elegant, clear,

Target Market(s)

young professional, caucasian , young mothers.

Industry/Entity Type

Business

```html
<!DOCTYPE html>
<html lang="en">
<head>
<meta charset="utf-8">
<title>Velora Hypnotherapy – Business Card</title>
<link rel="stylesheet" href="https://fonts.googleapis.com/css2?family=Quicksand:wght@500;600;700&family=Roboto+Condensed:wght@400;700&display=swap">
<style>
  :root {
    --page: #e7ebee;
    --card: #f7f8f9;
    --blue: #3d84cc;
    --blue-deep: #2f74bd;
    --blue-soft: #8dbbe6;
    --ink: #2a2d31;
    --muted: #55595e;
    --white: #ffffff;
    --badge: #c9d63a;
  }
  * { box-sizing: border-box; margin: 0; padding: 0; }
  html, body { width: 1200px; height: 960px; overflow: hidden; }
  body {
    background: var(--page);
    display: flex;
    align-items: center;
    justify-content: center;
    gap: 80px;
    font-family: "Quicksand", sans-serif;
    color: var(--ink);
  }
  .card {
    position: relative;
    background: var(--card);
    border-radius: 24px;
    overflow: hidden;
    box-shadow: 0 10px 28px rgba(30, 45, 60, .18);
  }

  /* Front */
  .card-front { width: 560px; height: 320px; }
  .front-top { position: absolute; inset: 0 0 auto 0; height: 150px; }
  .brand-name {
    position: absolute; left: 40px; top: 44px;
    font-size: 31px; font-weight: 600; color: var(--blue-deep);
    display: flex; align-items: center; gap: 10px;
  }
  .brand-dot { width: 14px; height: 14px; border-radius: 50%; background: var(--blue-deep); }
  .brand-url {
    position: absolute; left: 64px; top: 90px;
    font-size: 12.5px; font-weight: 600; letter-spacing: .6px; color: var(--muted);
    border-top: 2px solid var(--blue); padding-top: 3px;
  }
  .member-badge {
    position: absolute; right: 36px; top: 26px;
    width: 82px; height: 82px; border-radius: 50%;
    background: radial-gradient(circle, var(--badge) 0 55%, #7fb53a 100%);
    border: 3px solid var(--white);
    box-shadow: 0 0 0 2px #6e8a34;
  }
  .stripe-soft { position: absolute; left: 0; right: 0; top: 150px; height: 10px; background: var(--blue-soft); }
  .stripe-white { position: absolute; left: 0; right: 0; top: 160px; height: 4px; background: var(--white); }
  .front-band {
    position: absolute; left: 0; right: 0; top: 164px; bottom: 0;
    background: radial-gradient(circle at 45% 70%, #4a8fd4 0%, var(--blue) 45%, var(--blue-deep) 100%);
  }
  .holder { position: absolute; left: 188px; top: 44px; text-align: right; color: var(--white); }
  .holder-name { font-size: 30px; font-weight: 600; }
  .holder-role { font-size: 15px; font-weight: 500; margin-top: 2px; }
  .contact { position: absolute; right: 34px; top: 30px; color: var(--white); font-size: 13.5px; font-weight: 500; }
  .contact li { list-style: none; display: flex; align-items: center; gap: 7px; margin-bottom: 8px; }
  .contact svg { width: 12px; height: 14px; fill: none; stroke: var(--white); stroke-width: 1.6; }

  /* Back */
  .card-back { width: 320px; height: 560px; font-family: "Roboto Condensed", sans-serif; }
  .back-head { padding: 30px 30px 0; }
  .back-brand { font-family: "Quicksand", sans-serif; font-size: 26px; font-weight: 600; color: var(--blue-deep); }
  .back-detail { font-size: 13px; color: var(--ink); margin-top: 6px; line-height: 1.45; }
  .appointments-title { text-align: center; font-weight: 700; font-size: 15px; margin: 22px 0 14px; }
  .appointments { padding: 0 30px; }
  .slot { display: flex; align-items: flex-end; gap: 4px; font-size: 13px; color: var(--muted); height: 30px; }
  .slot .line { border-bottom: 1px solid var(--muted); height: 14px; }
  .slot .time { width: 22px; }
  .slot .day { flex: 1; }
  .slot .date { width: 54px; }
  .back-band {
    position: absolute; left: 0; right: 0; top: 400px; height: 76px;
    background: radial-gradient(circle at 50% 60%, #4a8fd4 0%, var(--blue) 50%, var(--blue-deep) 100%);
  }
  .back-note { position: absolute; left: 22px; right: 22px; top: 488px; font-size: 9px; color: var(--ink); line-height: 1.4; }
  .back-note .reg { font-size: 11px; margin-top: 6px; }
</style>
</head>
<body>

  <section class="card card-front" aria-label="Business card front">
    <div class="front-top">
      <div class="brand-name"><span class="brand-dot"></span>Velora Hypnotherapy</div>
      <div class="brand-url">www.veloraclinicalhypnotherapy.com.au</div>
      <div class="member-badge" role="img" aria-label="Professional association membership badge"></div>
    </div>
    <div class="stripe-soft"></div>
    <div class="stripe-white"></div>
    <div class="front-band">
      <div class="holder">
        <div class="holder-name">Daniel Wexford</div>
        <div class="holder-role">Psychotherapy &amp; Hypnosis</div>
      </div>
      <ul class="contact">
        <li><svg viewBox="0 0 12 14"><rect x="2.5" y="1" width="7" height="12" rx="1.5"/><line x1="5" y1="11" x2="7" y2="11"/></svg>842 61 937</li>
        <li><svg viewBox="0 0 12 14"><rect x="1" y="3" width="10" height="10" rx="1.5"/><rect x="3" y="1" width="6" height="4" rx="1"/><line x1="4" y1="8" x2="8" y2="8"/><line x1="4" y1="10.5" x2="8" y2="10.5"/></svg>0427 591 628</li>
      </ul>
    </div>
  </section>

  <section class="card card-back" aria-label="Business card back – appointment card">
    <div class="back-head">
      <div class="back-brand">Velora Hypnotherapy</div>
      <p class="back-detail">By Appointment : Phone: 0427 591 628<br>148 Harlow Street, Kensbrook 3021<br>hello@veloraclinicalhypnotherapy.com.au</p>
    </div>
    <h2 class="appointments-title">Your Appointments</h2>
    <div class="appointments">
      <div class="slot">1. <span class="line time"></span>am/pm <span class="line day"></span><span class="line date"></span></div>
      <div class="slot">2. <span class="line time"></span>am/pm <span class="line day"></span><span class="line date"></span></div>
      <div class="slot">3. <span class="line time"></span>am/pm <span class="line day"></span><span class="line date"></span></div>
      <div class="slot">4. <span class="line time"></span>am/pm <span class="line day"></span><span class="line date"></span></div>
      <div class="slot">5. <span class="line time"></span>am/pm <span class="line day"></span><span class="line date"></span></div>
    </div>
    <div class="back-band"></div>
    <div class="back-note">
      <p>To reschedule your appointment, please SMS or phone<br>0427 591 628 at least 24 hours prior to your allocated time. Thank you.</p>
      <p class="reg">NHRA Registration No. NPR048217</p>
    </div>
  </section>

</body>
</html>
```